Haulage company, lets use ruby red white and some 3rd color for web design. and Garvel Pryce Transport logo

Target Market(s)

Transport industry

Industry/Entity Type

transport

Number of Pages Required

2 page

Requirements
Must have
• Logo

```html
<!DOCTYPE html>
<html lang="en">
<head>
<meta charset="utf-8">
<title>Garvel Pryce Transport</title>
<link rel="stylesheet" href="https://fonts.googleapis.com/css2?family=Titillium+Web:ital,wght@0,600;0,700;1,700&family=Open+Sans:wght@400;600&display=swap">
<style>
:root{
  --ruby:#c0112f;
  --ruby-soft:#f7dde2;
  --ink:#111111;
  --charcoal:#232323;
  --text:#444444;
  --muted:#555555;
  --paper:#ffffff;
  --mist:#f4f4f4;
  --star:#f5a623;
}
*{margin:0;padding:0;box-sizing:border-box}
html,body{width:1200px;height:3437px;overflow:hidden}
body{position:relative;background:var(--paper);font-family:"Open Sans",sans-serif;color:var(--text)}
.abs{position:absolute}
.heading{font-family:"Titillium Web",sans-serif;font-weight:700;text-transform:uppercase}
.btn{position:absolute;display:flex;align-items:center;justify-content:center;background:var(--ruby);color:#fff;font-family:"Titillium Web",sans-serif;font-weight:700;font-size:16px;border-radius:3px;text-transform:uppercase}

/* header */
.site-header{top:0;left:0;width:1200px;height:69px;background:var(--ink)}
.brand{left:113px;top:19px;color:#fff;font-family:"Titillium Web",sans-serif;font-weight:700;font-size:25px;letter-spacing:.3px}
.nav{left:667px;top:22px;display:flex;gap:25px;font-size:16px;color:#fff}
.nav .active{border-bottom:2px solid var(--ruby);padding-bottom:4px}
.login{left:998px;top:16px;width:91px;height:40px;border:1.5px solid #fff;border-radius:3px;color:#fff;font-family:"Titillium Web",sans-serif;font-weight:700;font-size:16px;display:flex;align-items:center;justify-content:center}

/* hero */
.hero{top:69px;left:0;width:1200px;height:429px;background:linear-gradient(100deg,#0c0d10 0%,#2a2e33 35%,#8c8f93 62%,#cfd0cf 78%,#6b6256 100%)}
.hero-title{left:111px;top:164px;color:#fff;font-size:52px;line-height:64px}
.hero-title em{color:var(--ruby);font-style:italic}
.hero-btn{left:111px;top:316px;width:133px;height:40px;border:1.5px solid #fff;border-radius:3px;color:#fff;font-family:"Titillium Web",sans-serif;font-weight:700;font-size:15px;display:flex;align-items:center;justify-content:center}
.dot{left:50px;width:6px;height:6px;border-radius:50%;background:#fff}

/* section titles */
.section-title{left:0;width:1200px;text-align:center;color:var(--ruby);font-size:50px;line-height:60px}

/* services */
.service-icon{width:64px;height:72px}
.service-name{color:#3a3a3a;font-size:25px;line-height:34px;font-family:"Titillium Web",sans-serif;font-weight:600;text-transform:uppercase;letter-spacing:.5px}
.service-copy{width:380px;font-size:15.5px;line-height:28px;color:var(--muted)}

/* about */
.about{top:1298px;left:0;width:1200px;height:527px;background:var(--ink)}
.about-frame{left:123px;top:1376px;width:327px;height:393px;border:1px solid var(--ruby)}
.about-photo{left:111px;top:1366px;width:326px;height:391px;background:linear-gradient(160deg,#8b8f93 0%,#d9dadb 40%,#efefef 60%,#7a2a34 85%,#5a5e61 100%)}
.about-title{left:574px;top:1372px;color:#fff;font-size:52px}
.about-copy{left:574px;top:1460px;width:520px;color:#fff;font-size:15.5px;line-height:28.5px}
.about-copy p+p{margin-top:13px}

/* testimonials */
.quote-card{top:2027px;width:466px;height:220px;border:1.5px solid var(--ruby);border-top-color:#555;border-right-color:#555;border-bottom-color:#555}
.quote-mark{position:absolute;right:36px;top:-20px;background:#fff;padding:0 6px;font-family:"Titillium Web",sans-serif;font-weight:700;font-size:64px;line-height:40px;height:40px;color:#333}
.quote-name{position:absolute;left:35px;top:24px;font-size:22px;color:#222}
.stars{position:absolute;left:37px;top:62px;color:var(--star);font-size:13px;letter-spacing:5px}
.quote-copy{position:absolute;left:37px;top:102px;width:390px;font-size:15.5px;line-height:28.5px;color:var(--muted)}
.arrow{top:2104px;width:48px;height:48px}

/* updates */
.updates{top:2332px;left:0;width:1200px;height:760px;background:var(--mist)}
.post-photo{top:2499px;width:315px;height:325px}
.post-card{top:2698px;width:293px;height:239px;background:#fff;box-shadow:0 2px 10px rgba(0,0,0,.08);padding:24px 27px}
.post-date{color:var(--ruby);font-size:15.5px}
.post-title{margin-top:12px;color:#222;font-size:15.5px;line-height:26px}
.post-copy{margin-top:8px;color:var(--muted);font-size:15.5px;line-height:26px}
.post-foot{position:absolute;left:27px;right:27px;bottom:28px;display:flex;justify-content:space-between;align-items:center}
.read-more{color:var(--ruby);font-family:"Titillium Web",sans-serif;font-weight:700;font-size:14px;text-decoration:underline}

/* footer */
.site-footer{top:3092px;left:0;width:1200px;height:345px;background:var(--charcoal);color:#fff}
.foot-head{top:3176px;font-size:17px;font-family:"Titillium Web",sans-serif;font-weight:600;text-transform:uppercase;color:#fff;letter-spacing:.3px}
.foot-list{top:3223px;font-size:16px;line-height:29px;color:#fff;list-style:none}
.contact-row{left:112px;display:flex;gap:16px;font-size:16px;line-height:26px;color:#fff}
.contact-row svg{flex:none;margin-top:5px}
.email-field{left:838px;top:3229px;width:251px;height:39px;background:#fff;border-radius:2px;color:#333;font-size:15px;padding:9px 27px}
.copyright{left:0;top:3358px;width:1200px;text-align:center;font-size:15.5px;color:#cfcfcf}
</style>
</head>
<body>

<header class="abs site-header">
  <div class="abs brand">GARVEL PRYCE TRANSPORT</div>
  <nav class="abs nav"><span class="active">Home</span><span>Services</span><span>Tracking</span><span>Support</span></nav>
  <div class="abs login">LOGIN</div>
</header>

<section class="abs hero" role="img" aria-label="Articulated lorry with a refrigerated trailer driving along a motorway"></section>
<h1 class="abs heading hero-title">Seamless <em>End-to-End</em><br>Logistics Solutions</h1>
<div class="abs hero-btn">LEARN MORE</div>
<div class="abs dot" style="top:251px;width:9px;height:9px;left:48px;background:var(--ruby)"></div>
<div class="abs dot" style="top:274px"></div>
<div class="abs dot" style="top:293px"></div>
<div class="abs dot" style="top:312px"></div>

<h2 class="abs heading section-title" style="top:557px">Our Services</h2>

<!-- service: fulfilment -->
<svg class="abs service-icon" style="left:110px;top:700px" viewBox="0 0 64 72" fill="none" stroke="#222" stroke-width="2">
  <circle cx="44" cy="50" r="18" fill="#f7dde2" stroke="none"/>
  <rect x="20" y="2" width="14" height="12"/><rect x="12" y="14" width="14" height="14"/><rect x="28" y="14" width="14" height="14"/>
  <rect x="4" y="28" width="20" height="14"/><rect x="26" y="28" width="20" height="14"/>
  <path d="M2 44h60M2 50h60M6 50v6M32 50v6M58 50v6"/>
</svg>
<div class="abs service-name" style="left:205px;top:700px">Fulfilment and<br>Warehousing</div>
<p class="abs service-copy" style="left:205px;top:778px">Duis aute irure dolor in reprehenderit in voluptate velit esse cillum dolore eu fnulla pariatur. Excepteur sint occaecat cupidatat non proident.</p>
<div class="btn" style="left:204px;top:880px;width:132px;height:38px">LEARN MORE</div>

<!-- service: international -->
<svg class="abs service-icon" style="left:621px;top:700px" viewBox="0 0 64 72" fill="none" stroke="#222" stroke-width="2">
  <circle cx="44" cy="50" r="18" fill="#f7dde2" stroke="none"/>
  <circle cx="32" cy="34" r="30"/>
  <path d="M10 20c8 4 12 0 18 6s-2 10 4 14M40 6c-2 8 6 10 14 12"/>
  <rect x="14" y="36" width="18" height="14" fill="#fff"/><path d="M32 40h8l5 6v4H32z" fill="#fff"/>
  <circle cx="20" cy="52" r="3" fill="#fff"/><circle cx="38" cy="52" r="3" fill="#fff"/>
</svg>
<div class="abs service-name" style="left:716px;top:700px">International<br>Deliveries</div>
<p class="abs service-copy" style="left:716px;top:778px">Duis aute irure dolor in reprehenderit in voluptate velit esse cillum dolore eu fnulla pariatur. Excepteur sint occaecat cupidatat non proident.</p>
<div class="btn" style="left:716px;top:880px;width:132px;height:38px">LEARN MORE</div>

<!-- service: freight -->
<svg class="abs service-icon" style="left:110px;top:992px" viewBox="0 0 64 72" fill="none" stroke="#222" stroke-width="2">
  <circle cx="44" cy="48" r="18" fill="#f7dde2" stroke="none"/>
  <rect x="4" y="12" width="38" height="26" fill="#fff"/>
  <path d="M10 16v18M16 16v18M22 16v18M28 16v18M34 16v18"/>
  <path d="M42 20h10l8 10v10H42z" fill="#fff"/><path d="M46 24h5l5 6h-10z"/>
  <circle cx="14" cy="40" r="4" fill="#fff"/><circle cx="50" cy="40" r="4" fill="#fff"/>
</svg>
<div class="abs service-name" style="left:205px;top:992px">Freight<br>Forwarding</div>
<p class="abs service-copy" style="left:205px;top:1070px">Duis aute irure dolor in reprehenderit in voluptate velit esse cillum dolore eu fnulla pariatur. Excepteur sint occaecat cupidatat non proident.</p>
<div class="btn" style="left:204px;top:1172px;width:132px;height:38px">LEARN MORE</div>

<!-- service: sourcing -->
<svg class="abs service-icon" style="left:621px;top:992px" viewBox="0 0 64 72" fill="none" stroke="#222" stroke-width="2">
  <circle cx="46" cy="50" r="18" fill="#f7dde2" stroke="none"/>
  <rect x="18" y="38" width="28" height="22" rx="2" fill="#fff"/>
  <path d="M22 38V24l-10-8M32 38V10M42 38V24l10-8M18 46H8M46 46h10M24 54h16"/>
  <circle cx="10" cy="14" r="3"/><circle cx="32" cy="6" r="3"/><circle cx="54" cy="14" r="3"/><circle cx="6" cy="46" r="2"/><circle cx="58" cy="46" r="2"/>
</svg>
<div class="abs service-name" style="left:716px;top:992px">Sourcing and<br>Procurement</div>
<p class="abs service-copy" style="left:716px;top:1070px">Duis aute irure dolor in reprehenderit in voluptate velit esse cillum dolore eu fnulla pariatur. Excepteur sint occaecat cupidatat non proident.</p>
<div class="btn" style="left:716px;top:1172px;width:132px;height:38px">LEARN MORE</div>

<!-- about -->
<section class="abs about"></section>
<div class="abs about-frame"></div>
<div class="abs about-photo" role="img" aria-label="White and maroon lorry cab parked in a yard"></div>
<h2 class="abs heading about-title">About Us</h2>
<div class="abs about-copy">
  <p>Lorem ipsum dolor sit amet, consectetur adipiscing elit, sed do eiusmod tempor incididunt ut labore et dolore magna aliqua. Quis ipsum endisse ultrices gravida. Risus commodo viverra maecen lacus vel facilisis.</p>
  <p>Sed ut perspiciatis unde omnis iste natus error sit voluptatem accusan tium doloremque laudantium, totam rem aperiam, eaque ipsa quae ab illo inventore veritatis et quasi architecto beatae vitae dicta sunt explica bo. Nemo enim ipsam voluptatem quia voluptas sit aspernatur</p>
</div>
<div class="btn" style="left:574px;top:1711px;width:132px;height:39px">LEARN MORE</div>

<!-- testimonials -->
<h2 class="abs heading section-title" style="top:1900px">Client Testimonials</h2>
<svg class="abs arrow" style="left:29px" viewBox="0 0 48 48" fill="none" stroke="#999" stroke-width="2"><circle cx="24" cy="24" r="22"/><path d="M27 15l-9 9 9 9"/></svg>
<svg class="abs arrow" style="left:1121px" viewBox="0 0 48 48" fill="none" stroke="#999" stroke-width="2"><circle cx="24" cy="24" r="22"/><path d="M21 15l9 9-9 9"/></svg>
<div class="abs quote-card" style="left:111px">
  <span class="quote-mark">&#8221;</span>
  <div class="quote-name">Patty</div>
  <div class="stars">★★★★★</div>
  <p class="quote-copy">Lorem ipsum dolor sit amet, consectetur adipiscing elit, sed do eiusmod tempor incididunt lare et dolore magna aliq enim ad minim veniam, quis nostrud.</p>
</div>
<div class="abs quote-card" style="left:623px">
  <span class="quote-mark">&#8221;</span>
  <div class="quote-name">Patty</div>
  <div class="stars">★★★★★</div>
  <p class="quote-copy">Lorem ipsum dolor sit amet, consectetur adipiscing elit, sed do eiusmod tempor incididunt lare et dolore magna aliq enim ad minim veniam, quis nostrud.</p>
</div>

<!-- updates -->
<section class="abs updates"></section>
<h2 class="abs heading section-title" style="top:2389px">Our Latest Updates</h2>

<div class="abs post-photo" style="left:111px;background:linear-gradient(180deg,#c9d2d8 0%,#e9eaeb 45%,#a33a48 70%,#5d6a55 100%)" role="img" aria-label="Lorry cabs parked beside a field"></div>
<div class="abs post-photo" style="left:442px;background:linear-gradient(180deg,#2b2a2c 0%,#8e8c88 35%,#d7d3cb 55%,#7a2630 80%,#3a3a3a 100%)" role="img" aria-label="Two lorries parked at night"></div>
<div class="abs post-photo" style="left:773px;background:linear-gradient(180deg,#6f8fae 0%,#d6a98c 30%,#e9e3cf 50%,#8c2030 78%,#2e3a2a 100%)" role="img" aria-label="Lorry cab at sunset"></div>

<article class="abs post-card" style="left:123px">
  <div class="post-date">June 04, 2024</div>
  <div class="post-title">Nemo enim ipsam voluptatem quia voluptas sit aspernatur</div>
  <div class="post-copy">Sed ut perspiciatis unde omni iste natus error sit voluptatem.</div>
  <div class="post-foot"><span class="read-more">READ MORE</span>
    <svg width="20" height="20" viewBox="0 0 20 20" fill="#333"><circle cx="15" cy="4" r="3"/><circle cx="5" cy="10" r="3"/><circle cx="15" cy="16" r="3"/><path d="M5 10L15 4M5 10l10 6" stroke="#333" stroke-width="1.8"/></svg></div>
</article>
<article class="abs post-card" style="left:454px">
  <div class="post-date">June 04, 2024</div>
  <div class="post-title">Nemo enim ipsam voluptatem quia voluptas sit aspernatur</div>
  <div class="post-copy">Sed ut perspiciatis unde omni iste natus error sit voluptatem.</div>
  <div class="post-foot"><span class="read-more">READ MORE</span>
    <svg width="20" height="20" viewBox="0 0 20 20" fill="#333"><circle cx="15" cy="4" r="3"/><circle cx="5" cy="10" r="3"/><circle cx="15" cy="16" r="3"/><path d="M5 10L15 4M5 10l10 6" stroke="#333" stroke-width="1.8"/></svg></div>
</article>
<article class="abs post-card" style="left:785px">
  <div class="post-date">June 04, 2024</div>
  <div class="post-title">Nemo enim ipsam voluptatem quia voluptas sit aspernatur</div>
  <div class="post-copy">Sed ut perspiciatis unde omni iste natus error sit voluptatem.</div>
  <div class="post-foot"><span class="read-more">READ MORE</span>
    <svg width="20" height="20" viewBox="0 0 20 20" fill="#333"><circle cx="15" cy="4" r="3"/><circle cx="5" cy="10" r="3"/><circle cx="15" cy="16" r="3"/><path d="M5 10L15 4M5 10l10 6" stroke="#333" stroke-width="1.8"/></svg></div>
</article>
<div class="btn" style="left:534px;top:2996px;width:132px;height:39px">VIEW MORE</div>

<!-- footer -->
<footer class="abs site-footer"></footer>
<div class="abs foot-head" style="left:112px">Contact Us</div>
<div class="abs foot-head" style="left:443px">Quick Links</div>
<div class="abs foot-head" style="left:641px">Other Links</div>
<div class="abs foot-head" style="left:838px">Subscribe</div>

<div class="abs contact-row" style="top:3218px">
  <svg width="14" height="18" viewBox="0 0 14 18" fill="#fff"><path d="M7 0a7 7 0 0 0-7 7c0 5 7 11 7 11s7-6 7-11a7 7 0 0 0-7-7zm0 10a3 3 0 1 1 0-6 3 3 0 0 1 0 6z"/></svg>
  <span>Garvel Pryce Transport,<br>Address comes here</span>
</div>
<div class="abs contact-row" style="top:3283px">
  <svg width="15" height="15" viewBox="0 0 16 16" fill="#fff"><path d="M3.6 1l2.6 3-1.5 1.8a10 10 0 0 0 5.5 5.5L12 9.8l3 2.6-1.4 2.6C7 15 1 9 1 2.4z"/></svg>
  <span>+1888-555-0142</span>
</div>
<div class="abs contact-row" style="top:3317px">
  <svg width="15" height="12" viewBox="0 0 16 12" fill="#fff"><path d="M0 0h16v1.5L8 6.5 0 1.5zM0 3.3l8 5 8-5V12H0z"/></svg>
  <span>info@garvelprycetransport.com</span>
</div>

<ul class="abs foot-list" style="left:443px"><li>Home</li><li>Services</li><li>Tracking</li><li>Support</li></ul>
<ul class="abs foot-list" style="left:641px"><li>Privacy Policy</li><li>Terms &amp; Services</li><li>FAQ</li></ul>

<div class="abs email-field">Email ID</div>
<div class="btn" style="left:838px;top:3282px;width:133px;height:38px">VIEW MORE</div>

<div class="abs copyright">2024 Garvel Pryce Transport. All Rights Reserved.</div>

</body>
</html>
```